ULMIRA card Technical Architecture

Hello everyone ULMIRA: It is a consulting firm in Architecture and Construction. I require a card duplexing, sober, elegant, classic but not boring. Update 1: Use the following data for the card. Name: Gonzalo Pereda Mauricio Villalta Position: COO Twitter: @ulmiraAT Homepage: ulmira-example.com home address not include the participation of all thank you.

Target Market(s)

Construction companies, Architects and Consulting Engineers

Industry/Entity Type

Consulting

Contact Information for Business Card

Los campos que debe tener:
Nombre, Cargo, email, homepage y twitter

Font styles to use
Serif
Sans Serif
Other font styles liked:
• Me gustan playfair display, open sans y roboto, pero estoy sujeto a sus propuestas

Requirements
Must have
• Colors: Present combined proposals in white, red, gray and black Update 1: The two names must be clearly differentiated from the two surnames
Nice to have
• They are free to present their best proposals. I will bring them immediate feedback to the extent you can go see their designs. Complete data for card and logo files will give the winner the

```html
<!DOCTYPE html>
<html lang="es">
<head>
<meta charset="utf-8">
<title>ULMIRA — Tarjeta de presentación</title>
<link rel="stylesheet" href="https://fonts.googleapis.com/css2?family=Open+Sans:wght@300;400;600&display=swap">
<style>
  :root {
    --backdrop: #3a332f;
    --card: #1f1f20;
    --card-front: #242425;
    --red: #c8161d;
    --red-soft: #e0424a;
    --white: #f2f2f2;
    --grey: #c9c9c9;
    --rule: #4a4a4b;
  }
  * { box-sizing: border-box; margin: 0; padding: 0; }
  html, body {
    width: 1200px; height: 844px; overflow: hidden;
    background: var(--backdrop);
    font-family: "Open Sans", Arial, sans-serif;
  }
  .canvas {
    position: relative; width: 1200px; height: 844px;
  }
  .card {
    position: absolute; top: 272px;
    width: 525px; height: 300px;
    border-radius: 3px;
    box-shadow: 0 10px 26px rgba(0,0,0,.45);
  }
  /* Contact side */
  .card--contact { left: 50px; background: var(--card); }
  .card--contact .brand-mark {
    position: absolute; left: 0; top: 0; width: 262px; height: 300px;
    display: flex; align-items: center; justify-content: center; gap: 12px;
  }
  .brand-mark__square { width: 14px; height: 14px; background: var(--red); }
  .brand-mark__name {
    color: var(--red); font-weight: 600; font-size: 30px; letter-spacing: 4px;
  }
  .card--contact .divider {
    position: absolute; left: 268px; top: 60px; width: 1px; height: 180px;
    background: var(--rule);
  }
  .details {
    position: absolute; left: 292px; top: 66px; color: var(--white);
  }
  .details__name {
    color: var(--red); font-weight: 600; font-size: 17px; letter-spacing: .5px;
    text-transform: uppercase; line-height: 1.1;
  }
  .details__role { font-size: 13px; color: var(--grey); margin-top: 2px; }
  .details__contacts { margin-top: 18px; list-style: none; font-size: 13px; line-height: 1.55; }
  .details__contacts li { display: flex; align-items: center; gap: 8px; }
  .details__contacts svg { width: 10px; height: 10px; fill: var(--red); flex: none; }
  .details__web { margin-top: 16px; list-style: none; font-size: 13px; line-height: 1.5; }

  /* Brand side */
  .card--brand { left: 625px; background: var(--card-front); }
  .lockup {
    position: absolute; left: 0; right: 0; top: 104px;
    display: flex; flex-direction: column; align-items: center;
  }
  .lockup__row { display: flex; align-items: center; gap: 14px; }
  .lockup__square { width: 14px; height: 14px; background: var(--red); }
  .lockup__name {
    color: var(--white); font-weight: 400; font-size: 44px; letter-spacing: 12px;
    line-height: 1;
  }
  .lockup__rule { width: 290px; height: 1px; background: var(--grey); margin-top: 12px; opacity: .7; }
  .lockup__tagline {
    margin-top: 8px; color: var(--white); font-weight: 300; font-size: 15px;
    letter-spacing: 5px; text-transform: uppercase;
  }
</style>
</head>
<body>
<main class="canvas">
  <section class="card card--contact" aria-label="Cara de contacto">
    <div class="brand-mark">
      <span class="brand-mark__square"></span>
      <span class="brand-mark__name">ULMIRA</span>
    </div>
    <div class="divider"></div>
    <div class="details">
      <h1 class="details__name">Marcus Ellery</h1>
      <p class="details__role">Managing Director</p>
      <ul class="details__contacts">
        <li>
          <svg viewBox="0 0 10 10" aria-hidden="true"><path d="M2.5 0h5a1 1 0 0 1 1 1v8a1 1 0 0 1-1 1h-5a1 1 0 0 1-1-1V1a1 1 0 0 1 1-1zm.5 1.5v6h4v-6z"/></svg>
          (044)555010203
        </li>
        <li>
          <svg viewBox="0 0 10 10" aria-hidden="true"><path d="M0 2h10v6H0zm1 1v.3l4 2.5 4-2.5V3z"/></svg>
          info@ulmira-example.com
        </li>
      </ul>
      <ul class="details__web">
        <li>www.social-example.com</li>
        <li>www.ulmira-example.com</li>
      </ul>
    </div>
  </section>

  <section class="card card--brand" aria-label="Cara de marca">
    <div class="lockup">
      <div class="lockup__row">
        <span class="lockup__square"></span>
        <span class="lockup__name">ULMIRA</span>
      </div>
      <div class="lockup__rule"></div>
      <p class="lockup__tagline">Arquitectura Técnica</p>
    </div>
  </section>
</main>
</body>
</html>
```